Venture 482 - Lumora Book Cover

I am looking for a Lumora book cover for my book about "Venture 482".
The Book is Titled:
Venture 482 Ascended
Shaping Outcomes: Paths To Unlocking Cosmic Truths
Author is Dorian Pell
Here is a book description that may help you understand more about it:
Inspired by the genius of Edwin Marlowe, this comprehensive guide delves into the ancient wisdom and cutting-edge science behind the 482 method, a powerful tool for manifesting your desires. Whether you're seeking personal growth, financial success, or spiritual enlightenment, this book provides advanced techniques and methods to transform your dreams into reality.
Any questions please ask.
Thanks
Owen

```html
<!DOCTYPE html>
<html lang="en">
<head>
<meta charset="utf-8">
<title>Venture 482 Ascended — Dorian Pell</title>
<link rel="stylesheet" href="https://fonts.googleapis.com/css2?family=Anton&family=Montserrat:ital,wght@0,600;0,800;1,400&family=Stardos+Stencil:wght@700&display=swap">
<style>
  :root {
    --sky-top: #05090b;
    --sky-mid: #0a1d22;
    --sky-low: #12454c;
    --sky-glow: #1f6b72;
    --ink: #ffffff;
    --emblem-core: rgba(255,255,255,0.16);
    --emblem-edge: rgba(255,255,255,0);
  }
  * { margin: 0; padding: 0; box-sizing: border-box; }
  html, body { width: 805px; height: 1200px; overflow: hidden; background: var(--sky-top); }
  .cover {
    position: relative;
    width: 805px;
    height: 1200px;
    overflow: hidden;
    color: var(--ink);
    background:
      radial-gradient(ellipse 90% 45% at 50% 100%, var(--sky-glow) 0%, rgba(31,107,114,0) 70%),
      linear-gradient(180deg, var(--sky-top) 0%, var(--sky-top) 30%, var(--sky-mid) 58%, var(--sky-low) 100%);
  }
  .emblem {
    position: absolute;
    left: 430px;
    top: 190px;
    width: 330px;
    height: 340px;
    border-radius: 50%;
    background: radial-gradient(circle at 50% 50%, var(--emblem-core) 0%, rgba(255,255,255,0.07) 55%, var(--emblem-edge) 72%);
  }
  .title-kicker {
    position: absolute;
    left: 104px;
    top: 252px;
    font-family: "Montserrat", sans-serif;
    font-weight: 800;
    font-size: 82px;
    line-height: 1;
    letter-spacing: -1px;
  }
  .title-number {
    position: absolute;
    left: 186px;
    top: 318px;
    width: 456px;
    text-align: center;
    font-family: "Anton", sans-serif;
    font-size: 330px;
    line-height: 1;
    letter-spacing: -10px;
  }
  .title-edition {
    position: absolute;
    left: 0;
    width: 805px;
    top: 624px;
    text-align: center;
    font-family: "Montserrat", sans-serif;
    font-weight: 600;
    font-size: 50px;
    line-height: 1;
    letter-spacing: 27px;
    padding-left: 27px;
  }
  .subtitle {
    position: absolute;
    left: 0;
    width: 805px;
    top: 806px;
    text-align: center;
  }
  .subtitle-lead {
    font-family: "Montserrat", sans-serif;
    font-weight: 800;
    font-size: 38px;
    line-height: 46px;
  }
  .subtitle-body {
    margin-top: 6px;
    font-family: "Montserrat", sans-serif;
    font-style: italic;
    font-weight: 400;
    font-size: 37px;
    line-height: 43px;
  }
  .author {
    position: absolute;
    left: 0;
    width: 805px;
    top: 1060px;
    text-align: center;
    font-family: "Stardos Stencil", sans-serif;
    font-weight: 700;
    font-size: 92px;
    line-height: 1;
    letter-spacing: 14px;
    padding-left: 14px;
  }
</style>
</head>
<body>
  <main class="cover">
    <div class="emblem" role="img" aria-label="Sacred geometry emblem: concentric circles, triangles and radiating lines in fine white line work"></div>
    <h1>
      <span class="title-kicker">VENTURE</span>
      <span class="title-number">482</span>
      <span class="title-edition">ASCENDED</span>
    </h1>
    <p class="subtitle">
      <span class="subtitle-lead">SHAPING OUTCOMES:</span><br>
      <span class="subtitle-body">Paths to unlocking<br>cosmic truths</span>
    </p>
    <p class="author">DORIAN PELL</p>
  </main>
</body>
</html>
```